4th Generation Family Business Needs a New Card Design!

We are a family owned 4th Generation company. We are based in the Sydney, Australia area and we are desperately in need of a more modern and classy card. We are monumental masons who design, supply & erect lasting memorials throughout cemeteries in Sydney. Our customers are normally in a period of grieving. I have attached logo files that will need to be implemented on the card. Company was established 1935. Australian Owned and Operated. Card needs to be designed to PIXO.com specification.

Target Market(s)

Our target market is based upon people that a grieving for family members that have passed away. We also deal with alot of companies that own and operate cemeteries.

Industry/Entity Type

Business

Contact Information for Business Card

Simon Harcourt, Operations Manager, 0417293086, simon@harcourtmemorials.com.au
Lewis Harcourt, Director, 0491630572, lewis@harcourtmemorials.com.au
Phone # 02 9561 3048
Website: www.harcourtmemorials.com.au
Address: Suite 17, 8 Palfrey Lane, West Carlow, Sydney NSW 2156

Font styles to use
Serif
Decorative
Script

Requirements
Must have
• Would like to see the logo nicely implemented with a modern design. Embossed lettering would be a nice additive.

```html
<!DOCTYPE html>
<html lang="en">
<head>
<meta charset="utf-8">
<title>Harcourt Memorials – Business Card</title>
<link rel="stylesheet" href="https://fonts.googleapis.com/css2?family=Cinzel:wght@700&family=Tinos:wght@400;700&display=swap">
<style>
  :root {
    --bg: #2a2a2c;
    --card: #1f2023;
    --white: #f4f4f2;
    --gold: #e8b624;
    --divider: #8a8a8a;
  }
  * { margin: 0; padding: 0; box-sizing: border-box; }
  html, body {
    width: 1200px; height: 1189px; overflow: hidden;
    background: var(--bg);
  }
  .canvas {
    width: 1200px; height: 1189px;
    display: flex; flex-direction: column; align-items: center; justify-content: center;
    gap: 56px;
  }
  .card {
    position: relative;
    width: 880px; height: 520px;
    background: var(--card);
    border-radius: 30px;
    box-shadow: 0 10px 30px rgba(0,0,0,.45);
    overflow: hidden;
  }
  .brand {
    display: flex; flex-direction: column; align-items: center;
  }
  .brand-mark {
    display: block;
    background: var(--gold);
  }
  .brand-name {
    font-family: "Tinos", serif;
    font-weight: 400;
    color: var(--white);
    text-align: center;
    line-height: 1.1;
  }
  /* front */
  .card--front .brand {
    position: absolute; left: 0; right: 0; top: 70px;
  }
  .card--front .brand-mark { width: 96px; height: 96px; }
  .card--front .brand-name { font-size: 54px; margin-top: 26px; }
  .card--front .web-rule {
    position: absolute; left: 80px; right: 80px; top: 400px;
    display: flex; align-items: center; gap: 18px;
  }
  .web-rule .rule { flex: 1; height: 2px; background: var(--gold); }
  .web-rule .web {
    font-family: "Tinos", serif; font-weight: 700;
    color: var(--gold); font-size: 25px; letter-spacing: .5px;
  }
  /* back */
  .card--back .brand {
    position: absolute; left: 40px; top: 0; bottom: 0; width: 380px;
    justify-content: center;
  }
  .card--back .brand-mark { width: 110px; height: 110px; }
  .card--back .brand-name { font-size: 44px; margin-top: 24px; }
  .card--back .brand-rule {
    width: 340px; height: 2px; background: var(--gold); margin-top: 18px;
  }
  .card--back .divider {
    position: absolute; left: 450px; top: 100px; bottom: 100px;
    width: 2px; background: var(--divider);
  }
  .contact {
    position: absolute; left: 490px; top: 96px; right: 30px;
    font-family: "Tinos", serif; color: var(--white);
  }
  .contact .person {
    font-family: "Cinzel", serif; font-weight: 700;
    font-size: 30px; letter-spacing: 1px; line-height: 1;
  }
  .contact .role {
    color: var(--gold); font-weight: 700; font-size: 24px; margin-top: 2px;
  }
  .contact .address {
    font-size: 24px; line-height: 1.3; margin-top: 34px;
  }
  .contact .lines { margin-top: 12px; list-style: none; }
  .contact .lines li {
    display: flex; align-items: center; gap: 12px;
    font-size: 24px; line-height: 1; margin-bottom: 8px;
  }
  .icon {
    width: 26px; height: 26px; border-radius: 5px;
    background: var(--gold);
    display: inline-flex; align-items: center; justify-content: center;
    flex: none;
  }
  .icon svg { width: 18px; height: 18px; }
  .contact .website {
    color: var(--gold); font-weight: 700; font-size: 25px; margin-top: 10px;
  }
</style>
</head>
<body>
<main class="canvas">
  <section class="card card--front" aria-label="Card front">
    <div class="brand">
      <span class="brand-mark" aria-hidden="true"></span>
      <h1 class="brand-name">Harcourt Memorials</h1>
    </div>
    <div class="web-rule">
      <span class="rule"></span>
      <span class="web">www.harcourtmemorials.com.au</span>
      <span class="rule"></span>
    </div>
  </section>

  <section class="card card--back" aria-label="Card back">
    <div class="brand">
      <span class="brand-mark" aria-hidden="true"></span>
      <h2 class="brand-name">Harcourt Memorials</h2>
      <span class="brand-rule"></span>
    </div>
    <span class="divider"></span>
    <div class="contact">
      <p class="person">Simon Harcourt</p>
      <p class="role">Operations Manager</p>
      <p class="address">Suite 17, 8 Palfrey Lane,<br>West Carlow, Sydney NSW 2156</p>
      <ul class="lines">
        <li>
          <span class="icon"><svg viewBox="0 0 18 18"><rect x="5" y="2" width="8" height="14" rx="1.5" fill="none" stroke="#1f2023" stroke-width="1.6"/><line x1="8" y1="13.5" x2="10" y2="13.5" stroke="#1f2023" stroke-width="1.6"/></svg></span>
          0417293086
        </li>
        <li>
          <span class="icon"><svg viewBox="0 0 18 18"><path d="M5 2.5l2.5 3-1.5 1.8c.8 1.8 2.2 3.2 4 4l1.8-1.5 3 2.5-1.6 2.4C9 14.5 3.5 9 2.8 4.2z" fill="#1f2023"/></svg></span>
          02 9561 3048
        </li>
        <li>
          <span class="icon"><svg viewBox="0 0 18 18"><rect x="2" y="4" width="14" height="10" fill="none" stroke="#1f2023" stroke-width="1.6"/><path d="M2 4l7 6 7-6" fill="none" stroke="#1f2023" stroke-width="1.6"/></svg></span>
          simon@harcourtmemorials.com.au
        </li>
      </ul>
      <p class="website">www.harcourtmemorials.com.au</p>
    </div>
  </section>
</main>
</body>
</html>
```